Brisk Harbor claims recovery services

Its a new company in Dubai UAE. The company activity is debt management, debt collection, loans settlements and restructuring. The company involved in any business or sector requires debt management including government entities, Medical & Health care sector, Banks & finance companies, SME's and commercial business.

Target Market(s)

government entities, Medical & Health care sector, Banks & finance companies, SME's and commercial business.

Industry/Entity Type

Financial Service

Number of Pages Required

5+ page

Requirements
Must have
• Focus on the services not the team and clients
Should not have
• Colorful . Shouldn't have Client testimonial and our clients

```html
<!DOCTYPE html>
<html lang="en">
<head>
<meta charset="utf-8">
<title>Brisk Harbor — Claims Recovery Services</title>
<link rel="stylesheet" href="https://fonts.googleapis.com/css2?family=Cinzel:wght@600&family=Open+Sans:wght@400;600;700&display=swap">
<style>
:root{
  --brand:#0d5a85;
  --brand-dark:#0a4467;
  --footer:#0c4e77;
  --ink:#2b2b2b;
  --muted:#6d6d6d;
  --light:#f1f1f1;
  --white:#ffffff;
}
*{box-sizing:border-box;margin:0;padding:0}
html,body{width:1200px;height:2568px;overflow:hidden}
body{font-family:"Open Sans",Arial,sans-serif;color:var(--ink);background:var(--white);position:relative}

/* header */
.site-header{position:absolute;top:0;left:0;width:1200px;height:113px}
.brand{position:absolute;left:99px;top:30px;display:flex;align-items:center;gap:12px}
.brand-square{width:44px;height:44px;background:var(--brand)}
.brand-name{font-family:"Cinzel",Georgia,serif;font-weight:600;font-size:29px;color:var(--brand);line-height:1}
.brand-tag{font-size:9px;letter-spacing:3px;color:var(--brand);margin-top:4px}
.call{position:absolute;left:668px;top:40px;display:flex;align-items:center;gap:12px;font-size:13px;color:var(--muted)}
.call strong{color:var(--brand);font-size:16px}
.quote-btn{position:absolute;left:930px;top:38px;width:171px;height:41px;background:var(--brand-dark);color:var(--white);font-size:11.5px;font-weight:600;display:flex;align-items:center;justify-content:center;border-radius:2px}

/* nav */
.main-nav{position:absolute;top:113px;left:0;width:1200px;height:53px;background:linear-gradient(#b3b3b3,#9a9a9a)}
.main-nav ul{list-style:none;position:absolute;left:99px;width:1002px;height:53px;display:flex}
.main-nav li{flex:1;display:flex;align-items:center;justify-content:center;color:var(--white);font-size:12px}
.main-nav li.active{background:var(--brand)}

/* hero */
.hero{position:absolute;top:166px;left:0;width:1200px;height:502px;background:linear-gradient(100deg,#0c1c2b 0%,#1b2f44 45%,#2a3d52 70%,#121d2a 100%)}
.hero-title{position:absolute;left:99px;top:200px;display:flex;align-items:center;gap:18px;color:var(--white)}
.hero-mark{width:70px;height:70px;border:3px solid var(--white)}
.hero-title h1{font-family:"Cinzel",Georgia,serif;font-weight:600;font-size:29px;letter-spacing:1px}
.hero-title p{font-family:"Cinzel",Georgia,serif;font-size:19px;letter-spacing:1.5px;margin-top:6px}
.hero-arrow{position:absolute;top:228px}

/* mission vision */
.mv{position:absolute;top:668px;left:0;width:1200px;height:200px;display:flex}
.mv-block{flex:0 0 601px;padding:42px 80px 0;text-align:center;color:var(--white)}
.mv-block h2{font-weight:400;font-size:21px;margin-bottom:20px}
.mv-block p{font-size:11.5px;line-height:25px}
.mission{background:linear-gradient(#a9a9a9,#8f8f8f)}
.vision{flex:1;background:linear-gradient(var(--brand),var(--brand-dark))}

/* values */
.values{position:absolute;top:868px;left:0;width:1200px;height:390px;text-align:center}
.section-title{font-weight:400;font-size:21px;color:var(--ink)}
.values .section-title{margin-top:37px}
.section-lead{font-size:11.5px;color:var(--muted);line-height:22px;width:560px;margin:14px auto 0}
.value-line{position:absolute;top:197px;left:204px;width:794px;border-top:1px solid #dcdcdc}
.value{position:absolute;top:149px;width:250px;margin-left:-125px}
.value-ring{width:96px;height:96px;border-radius:50%;border:2px solid #cfcfcf;margin:0 auto;display:flex;align-items:center;justify-content:center;background:var(--white)}
.value-disc{width:84px;height:84px;border-radius:50%;background:#8d8d8d;display:flex;align-items:center;justify-content:center}
.value.active .value-ring{border-color:var(--brand)}
.value.active .value-disc{background:var(--brand)}
.value h3{font-size:12px;font-weight:600;margin-top:20px;color:var(--ink)}
.value.active h3{color:var(--brand)}
.value p{font-size:11px;color:var(--muted);line-height:22px;margin-top:8px;padding:0 22px}

/* about */
.about{position:absolute;top:1258px;left:0;width:1200px;height:317px;background:linear-gradient(90deg,#1e5f86,#2f6e93 50%,#1c5b80);color:var(--white);text-align:center}
.about .section-title{color:var(--white);font-size:25px;font-weight:600;margin-top:57px}
.about p{font-size:11.5px;line-height:26px;width:780px;margin:18px auto 0}
.about p + p{margin-top:14px}

/* services */
.services{position:absolute;top:1575px;left:0;width:1200px;height:712px;text-align:center}
.services .section-title{color:var(--brand);font-weight:600;font-size:25px;margin-top:36px}
.services .section-lead{width:640px;font-size:12.5px;margin-top:10px}
.svc-arrows{position:absolute;top:42px;left:1043px;display:flex;gap:8px}
.svc-arrows span{width:24px;height:24px;border:1px solid #ccc;display:flex;align-items:center;justify-content:center}
.card{position:absolute;top:147px;width:308px;height:367px;background:var(--light);border-bottom:3px solid #d5d5d5}
.card-image{height:186px;margin:4px}
.card-badge{width:36px;height:36px;background:var(--brand-dark);transform:rotate(45deg);border:3px solid var(--white);margin:-22px auto 0}
.card h3{font-size:13px;font-weight:600;color:var(--brand);margin-top:10px}
.card p{font-size:11px;line-height:21px;color:var(--muted);padding:0 24px;margin-top:6px}
.card-btn{position:absolute;left:94px;bottom:-22px;width:120px;height:40px;background:var(--brand-dark);color:var(--white);font-size:11px;font-weight:600;display:flex;align-items:center;justify-content:center}

/* footer */
.site-footer{position:absolute;top:2287px;left:0;width:1200px;height:281px;background:var(--footer);color:var(--white)}
.foot-col{position:absolute;top:34px}
.foot-brand{display:flex;align-items:center;gap:8px}
.foot-brand i{width:30px;height:30px;border:2px solid var(--white)}
.foot-brand b{font-family:"Cinzel",Georgia,serif;font-weight:600;font-size:19px}
.foot-col p{font-size:11.5px;line-height:22px}
.foot-col h4{font-size:14px;font-weight:600;margin-bottom:14px}
.foot-links{display:grid;grid-template-columns:70px 90px;font-size:11.5px;row-gap:8px}
.news-form{display:flex;margin-top:14px}
.news-input{width:168px;height:38px;background:#0a4163;font-size:11px;color:#b8cbd8;display:flex;align-items:center;padding-left:14px}
.news-btn{width:80px;height:38px;background:var(--white);color:var(--brand);font-size:15px;display:flex;align-items:center;justify-content:center}
.contact-row{display:flex;align-items:center;gap:14px;margin-top:14px;font-size:13px}
.contact-row.big{font-size:17px}
.foot-bottom{position:absolute;top:229px;left:99px;width:1002px;display:flex;justify-content:space-between;align-items:center;font-size:11px}
.social{display:flex;align-items:center;gap:8px}
.social i{width:28px;height:28px;border-radius:50%;background:var(--white);display:block}
</style>
</head>
<body>

<header class="site-header">
  <div class="brand">
    <div class="brand-square"></div>
    <div>
      <div class="brand-name">BRISK HARBOR</div>
      <div class="brand-tag">CLAIMS RECOVERY SERVICES</div>
    </div>
  </div>
  <div class="call">
    <svg width="34" height="34" viewBox="0 0 34 34"><circle cx="17" cy="17" r="15.5" fill="none" stroke="#0d5a85" stroke-width="2"/><path d="M12 10l3 0 1.5 4-2 1.5a9 9 0 0 0 4 4l1.5-2 4 1.5 0 3a2 2 0 0 1-2 2A13 13 0 0 1 10 12a2 2 0 0 1 2-2z" fill="#0d5a85"/></svg>
    <span>Call Us Today : <strong>(+111) 555-0142</strong></span>
  </div>
  <div class="quote-btn">REQUEST A QUOTE</div>
</header>

<nav class="main-nav">
  <ul>
    <li class="active">HOME</li><li>ABOUT US</li><li>SERVICES</li><li>OUR TEAM</li><li>CONTACT US</li>
  </ul>
</nav>

<section class="hero" role="img" aria-label="Businessman's hand stopping a row of falling wooden dominoes on a dark desk">
  <svg class="hero-arrow" style="left:58px" width="18" height="50" viewBox="0 0 18 50"><path d="M16 2L3 25l13 23" fill="none" stroke="#8a97a4" stroke-width="2"/></svg>
  <svg class="hero-arrow" style="left:1124px" width="18" height="50" viewBox="0 0 18 50"><path d="M2 2l13 23L2 48" fill="none" stroke="#8a97a4" stroke-width="2"/></svg>
  <div class="hero-title">
    <div class="hero-mark"></div>
    <div>
      <h1>MANAGING YOUR MONEY</h1>
      <p>RECOVERING YOUR RELATIONSHIPS</p>
    </div>
  </div>
</section>

<section class="mv">
  <div class="mv-block mission">
    <h2>MISSION</h2>
    <p>Brisk Harbor is a leading Debt Management and Claims Recovery Services company with a personal approach.We serve businesses and individuals in the pursuit of managing debt successfully, recovering monies swiftly, and salvaging valuable business relationships.</p>
  </div>
  <div class="mv-block vision">
    <h2>VISION</h2>
    <p>Our success is built on traditions of trust, valued relationships, and respect. We're reputed for our human approach to debt recovery and management, and are trusted by clients all over the region...</p>
  </div>
</section>

<section class="values">
  <h2 class="section-title">OUR VALUES</h2>
  <p class="section-lead">At Brisk Harbor, our values are born of time-honoured traditions, where business and trade were founded on trusting and mutually beneficial relationships.</p>
  <div class="value-line"></div>
  <div class="value active" style="left:204px">
    <div class="value-ring"><div class="value-disc">
      <svg width="34" height="34" viewBox="0 0 34 34" fill="none" stroke="#fff" stroke-width="4"><rect x="4" y="13" width="15" height="9" rx="4.5" transform="rotate(-45 11 17)"/><rect x="15" y="13" width="15" height="9" rx="4.5" transform="rotate(-45 22 17)"/></svg>
    </div></div>
    <h3>SOLID RELATIONSHIPS</h3>
    <p>Whether our clients come to us in a rare moment of crisis, or return to us again and again, our people take...</p>
  </div>
  <div class="value" style="left:466px">
    <div class="value-ring"><div class="value-disc">
      <svg width="36" height="30" viewBox="0 0 36 30" fill="#fff"><circle cx="18" cy="8" r="5"/><circle cx="7" cy="11" r="4"/><circle cx="29" cy="11" r="4"/><path d="M10 28a8 8 0 0 1 16 0z"/><path d="M0 27a7 7 0 0 1 11-5l-2 5zM36 27a7 7 0 0 0-11-5l2 5z"/></svg>
    </div></div>
    <h3>HONESTY AND INTEGRITY</h3>
    <p>From the very first point of contact with Brisk Harbor, you can be sure of our complete transparency...</p>
  </div>
  <div class="value" style="left:733px">
    <div class="value-ring"><div class="value-disc">
      <svg width="34" height="34" viewBox="0 0 34 34" fill="none" stroke="#fff"><circle cx="17" cy="17" r="12" stroke-width="7"/><circle cx="17" cy="17" r="12" stroke="#8d8d8d" stroke-width="7" stroke-dasharray="9 9.85" stroke-dashoffset="4.5"/></svg>
    </div></div>
    <h3>SINCERITY AND RESPECT</h3>
    <p>All members of the Brisk Harbor team are personally invested in looking after ourclients.</p>
  </div>
  <div class="value" style="left:998px">
    <div class="value-ring"><div class="value-disc">
      <svg width="34" height="30" viewBox="0 0 34 30" fill="#fff"><rect x="2" y="26" width="30" height="2"/><rect x="2" y="2" width="2" height="26"/><rect x="8" y="16" width="4" height="9"/><rect x="15" y="8" width="4" height="17"/><rect x="22" y="12" width="4" height="13"/></svg>
    </div></div>
    <h3>WISDOM AND UNDERSTANDING</h3>
    <p>Our team's combined experience across a wide range of business sectors gives Brisk Harbor...</p>
  </div>
</section>

<section class="about" role="img" aria-label="Smiling business team in an office, tinted blue behind the text">
  <h2 class="section-title">ABOUT US</h2>
  <p>Welcome to Brisk Harbor.We are a Claims Recovery and Debt Management Services company based in Dubai, United Arab Emirates. The Brisk Harbor team handles a comprehensive range of debt recoveries, such as invoices; insurance payments; supplier and rent payments; and personal and business loans, for individuals and businesses across an array of industries.</p>
  <p>Brisk Harbor was founded on traditional values, and we're proud of our personal approach. Our people are experienced, effective and efficient, but never compromise on providing a client-focused service.</p>
</section>

<section class="services">
  <h2 class="section-title">SERVICES</h2>
  <p class="section-lead">Intelligent lending opens doors and allows ambitious individuals and fledgling businesses to grow. But without careful planning and management, debt can become overwhelming.</p>
  <div class="svc-arrows">
    <span><svg width="8" height="10" viewBox="0 0 8 10"><path d="M6 1L2 5l4 4" fill="none" stroke="#999"/></svg></span>
    <span><svg width="8" height="10" viewBox="0 0 8 10"><path d="M2 1l4 4-4 4" fill="none" stroke="#999"/></svg></span>
  </div>

  <article class="card" style="left:99px">
    <div class="card-image" role="img" aria-label="Medical staff in white coats in a hospital corridor" style="background:linear-gradient(135deg,#cfe3ee,#eef3f6 50%,#9fc3da)"></div>
    <div class="card-badge"></div>
    <h3>HEALTH CARE</h3>
    <p>Our experience has taught us that when it comes to recovery, italways pays to find the most amicable solution, and...</p>
    <div class="card-btn">READ MORE</div>
  </article>
  <article class="card" style="left:445px">
    <div class="card-image" role="img" aria-label="Classical bank building with columns under a blue sky" style="background:linear-gradient(#4f7fb3,#9ab6d1 45%,#d8d2c2 60%,#6f8a5a)"></div>
    <div class="card-badge"></div>
    <h3>BANKS</h3>
    <p>Our experience has taught us that when it comes to recovery, italways pays to find the most amicable solution, and...</p>
    <div class="card-btn">READ MORE</div>
  </article>
  <article class="card" style="left:793px">
    <div class="card-image" role="img" aria-label="Silhouetted officials shaking hands beside a bright window" style="background:linear-gradient(135deg,#1e3f6e,#8fb1d9 55%,#e3edf7)"></div>
    <div class="card-badge"></div>
    <h3>GOVERNMENT SECTORS</h3>
    <p>Our experience has taught us that when it comes to recovery, italways pays to find the most amicable solution, and...</p>
    <div class="card-btn">READ MORE</div>
  </article>
</section>

<footer class="site-footer">
  <div class="foot-col" style="left:99px;top:42px;width:210px">
    <div class="foot-brand"><i></i><b>BRISK HARBOR</b></div>
    <p style="margin-top:18px">Sed ut perspiciatis unde omnis isteers accusantium doloremque laudantium, totam rem aperiam, eaque ipsa quae ab illo inventore veritatis et...</p>
  </div>
  <div class="foot-col" style="left:373px">
    <h4>NAVIGATION</h4>
    <div class="foot-links"><span>Home</span><span>Services</span><span>About Us</span><span>Contact Us</span><span>Team</span></div>
  </div>
  <div class="foot-col" style="left:588px;width:260px">
    <h4>NEWSLETTER</h4>
    <p>Excepteur sint occaecat cupidatat non proident, sunt in culpa qui officia deserunt mollit anim enim ipsam voluptatem quia...</p>
    <div class="news-form"><div class="news-input">Enter your email address</div><div class="news-btn">Sign Up</div></div>
  </div>
  <div class="foot-col" style="left:915px;width:200px">
    <h4>CONTACT US</h4>
    <p>4643#briskharbor Company name; Street name;City-4646</p>
    <div class="contact-row big">
      <svg width="20" height="20" viewBox="0 0 20 20"><path d="M4 2l3 0 1.5 4-2 1.5a9 9 0 0 0 4 4l1.5-2 4 1.5 0 3a2 2 0 0 1-2 2A13 13 0 0 1 2 4a2 2 0 0 1 2-2z" fill="none" stroke="#fff" stroke-width="1.4"/></svg>
      <span>(901) 555-0198</span>
    </div>
    <div class="contact-row">
      <svg width="20" height="14" viewBox="0 0 20 14"><rect x="1" y="1" width="18" height="12" fill="none" stroke="#fff" stroke-width="1.4"/><path d="M1 1l9 7 9-7" fill="none" stroke="#fff" stroke-width="1.4"/></svg>
      <span>info@briskharbor.example</span>
    </div>
  </div>
  <div class="foot-bottom">
    <span>Copyrights©briskharbor.2016 | Allrights Reserved.</span>
    <div class="social"><span style="margin-right:10px">Connect With Us:</span><i aria-label="Social link"></i><i aria-label="Social link"></i><i aria-label="Social link"></i></div>
  </div>
</footer>

</body>
</html>
```